Website for vegan focused blog

A website is needed so that I can launch my new blog in Dubai. It will be mainly vegan focused but also lifestyle based. Wordpress based- i started to build a site on Wordpress but design is not my forte ;)
Main content on the site will be; my recipes, reviews of products/restaurants, lifestyle posts and travel.
For this I ask for a homepage design, a recipe design page that includes a recipe card and a generic page for posts that can show pictures and videos. Also a contact me page.
Main headers should be: Home, Recipes and happy for suggestions.
Must look clean and neat but appealing, happy for minimalist look. I like pink and grey colours. Must be Wordpress compatible.
Have attached a couple of example posts for reference
Must have social links etc.
name of blog is: Maren by the dunes
Other blogs I like are: https://quietladleoven.com/ https://wellfernkitchen.com/ https://wellfernkitchen.com/ https://www.ohladycakes.com/https://beetsatsupper.com/ https://dorintalve.com/

Target Market(s)

Residents in the UAE. General individuals interested in vegan meals, plant based nutrition, travel and reviews.

Number of Pages Required

4 page

Colors
eea4c8
eda3c7
f9d9e8
dbdbdb
aaaaaa
d5d5d5

Requirements
Must have
• Recipe page- must include recipe card plug in option
• Social media integration
• Email sign ups

```html
<!DOCTYPE html>
<html lang="en">
<head>
<meta charset="utf-8">
<title>Maren by the dunes — Recipes</title>
<link href="https://fonts.googleapis.com/css2?family=Playfair+Display:ital,wght@0,400;1,400&family=Lato:wght@400;700&display=swap" rel="stylesheet">
<style>
:root{
  --pink:#eea4c8;
  --pink-soft:#f9d9e8;
  --pink-btn:#f7c6de;
  --line:#dbdbdb;
  --line-soft:#ececec;
  --grey:#aaaaaa;
  --ink:#444444;
  --footer-bg:#f8f8f8;
  --photo:linear-gradient(160deg,#e9d7c4 0%,#c8432f 22%,#5a2d2a 48%,#2f4a26 70%,#1f3318 100%);
  --sea:linear-gradient(180deg,#8d8d95 0%,#c9a790 38%,#5e6a72 55%,#2f3a3f 100%);
}
*{margin:0;padding:0;box-sizing:border-box}
html,body{width:859px;height:1200px;overflow:hidden;background:#fff}
body{position:relative;font-family:'Lato',sans-serif;color:var(--ink)}
.brand{font-family:'Playfair Display',serif;color:var(--pink);font-weight:400;text-align:center;position:absolute;left:0;width:859px}
.site-header .brand{top:28px;font-size:28px}
.main-nav{position:absolute;top:82px;left:0;width:859px;height:27px;border-top:1px solid var(--line-soft);border-bottom:1px solid var(--line-soft)}
.main-nav ul{list-style:none;position:absolute;left:241px;top:7px;display:flex}
.main-nav li{font-family:'Playfair Display',serif;font-style:italic;font-size:7.5px;letter-spacing:.5px;color:#333;margin-right:26px}
.main-nav li.active{color:var(--pink)}
.search-icon{position:absolute;right:54px;top:8px}
.recipe-section{position:absolute;left:168px;width:362px}
.section-title{position:relative;height:20px;text-align:center;font-size:13px;font-weight:400;line-height:20px}
.section-title::before,.section-title::after{content:"";position:absolute;top:9px;width:36%;height:3px;border-top:1px solid var(--line-soft);border-bottom:1px solid var(--line-soft)}
.section-title::before{left:0}.section-title::after{right:0}
.section-title span{font-family:'Playfair Display',serif;font-size:13px;font-weight:400;color:var(--pink);line-height:20px}
.recipe-grid{position:absolute;top:37px;left:0;display:grid;grid-template-columns:repeat(4,84px);column-gap:8.6px;row-gap:16px}
.recipe-card .thumb{height:54px;background:var(--photo)}
.recipe-card p{margin-top:9px;padding:0 9px;font-family:'Playfair Display',serif;font-style:italic;font-size:7px;line-height:8.5px;text-align:center;color:#666;height:17px}
.btn{display:block;background:var(--pink-btn);color:#fff;font-size:6px;text-align:center}
.recipe-section .btn{position:absolute;top:234px;left:0;width:65px;height:18px;line-height:18px}
.recipe-section .divider{position:absolute;top:261px;left:0;width:362px;border-top:1px solid var(--line-soft)}
.widget{position:absolute;left:557px;width:135px;border:1px solid var(--line-soft);padding:9px 9px}
.widget h3{font-family:'Playfair Display',serif;font-style:italic;font-weight:400;font-size:8px;color:var(--pink);margin-bottom:9px}
.about-photo{height:68px;background:var(--sea)}
.about p{font-size:5.2px;line-height:9px;text-align:center;margin-top:7px;color:#555}
.about .more{display:block;text-align:center;font-size:5.2px;margin-top:2px}
.socials{display:flex;justify-content:center;gap:7px}
.socials span{width:15px;height:15px;border-radius:50%;background:var(--pink-soft);border:1px solid var(--pink)}
.field{height:21px;border:1px solid var(--line);font-size:5px;color:var(--grey);padding:7px 8px;margin-bottom:9px}
.newsletter .btn{height:20px;line-height:20px;letter-spacing:.8px}
.photo-grid{display:grid;grid-template-columns:58px 58px;gap:2px;margin-bottom:9px}
.photo-grid div{height:58px;background:var(--photo)}
.photo-journal .btn{height:18px;line-height:18px}
.post{display:flex;gap:8px;margin-bottom:14px;height:30px}
.post .thumb{width:40px;height:30px;background:var(--photo);flex:none}
.post h4{font-family:'Playfair Display',serif;font-style:italic;font-weight:400;font-size:6px;line-height:8px;color:#444}
.post small{display:block;font-size:4.5px;letter-spacing:.6px;color:#888;margin-top:5px}
.site-footer{position:absolute;top:1056px;left:0;width:859px;height:144px;background:var(--footer-bg)}
.site-footer .brand{top:24px;font-size:24px}
.site-footer .socials{position:absolute;top:80px;left:0;width:859px}
.site-footer .socials span{width:17px;height:17px;background:var(--pink);border-color:var(--pink)}
.site-footer .copy{position:absolute;top:117px;left:0;width:859px;border-top:1px solid var(--line-soft);text-align:center;font-size:5.5px;color:var(--grey);padding-top:10px}
</style>
</head>
<body>
<header class="site-header">
  <div class="brand">Maren by the dunes</div>
  <nav class="main-nav">
    <ul>
      <li>Home</li><li>About</li><li class="active">Recipes</li><li>Reviews of products</li><li>Lifestyle</li><li>Travel</li><li>Contact</li>
    </ul>
    <svg class="search-icon" width="8" height="8" viewBox="0 0 8 8"><circle cx="3.3" cy="3.3" r="2.5" fill="none" stroke="#333" stroke-width="1"/><line x1="5.2" y1="5.2" x2="7.5" y2="7.5" stroke="#333" stroke-width="1"/></svg>
  </nav>
</header>

<main>
  <section class="recipe-section" style="top:136px">
    <h2 class="section-title"><span>Breakfasts</span></h2>
    <div class="recipe-grid">
      <article class="recipe-card"><div class="thumb" role="img" aria-label="Plated vegan dish photo"></div><p>Porttitor varius elit lacinia</p></article>
      <article class="recipe-card"><div class="thumb" role="img" aria-label="Plated vegan dish photo"></div><p>Nam consequat metus nisl (In varius)</p></article>
      <article class="recipe-card"><div class="thumb" role="img" aria-label="Plated vegan dish photo"></div><p>Imperdiet commodo</p></article>
      <article class="recipe-card"><div class="thumb" role="img" aria-label="Plated vegan dish photo"></div><p>Suspendisse nec tempus</p></article>
      <article class="recipe-card"><div class="thumb" role="img" aria-label="Plated vegan dish photo"></div><p>Porttitor varius elit lacinia</p></article>
      <article class="recipe-card"><div class="thumb" role="img" aria-label="Plated vegan dish photo"></div><p>Nam consequat metus nisl (In varius)</p></article>
      <article class="recipe-card"><div class="thumb" role="img" aria-label="Plated vegan dish photo"></div><p>Imperdiet commodo</p></article>
      <article class="recipe-card"><div class="thumb" role="img" aria-label="Plated vegan dish photo"></div><p>Suspendisse nec tempus</p></article>
    </div>
    <a class="btn">See more ⟶</a>
    <div class="divider"></div>
  </section>

  <section class="recipe-section" style="top:421px">
    <h2 class="section-title"><span>Entrées</span></h2>
    <div class="recipe-grid">
      <article class="recipe-card"><div class="thumb" role="img" aria-label="Plated vegan dish photo"></div><p>Porttitor varius elit lacinia</p></article>
      <article class="recipe-card"><div class="thumb" role="img" aria-label="Plated vegan dish photo"></div><p>Nam consequat metus nisl (In varius)</p></article>
      <article class="recipe-card"><div class="thumb" role="img" aria-label="Plated vegan dish photo"></div><p>Imperdiet commodo</p></article>
      <article class="recipe-card"><div class="thumb" role="img" aria-label="Plated vegan dish photo"></div><p>Suspendisse nec tempus</p></article>
      <article class="recipe-card"><div class="thumb" role="img" aria-label="Plated vegan dish photo"></div><p>Porttitor varius elit lacinia</p></article>
      <article class="recipe-card"><div class="thumb" role="img" aria-label="Plated vegan dish photo"></div><p>Nam consequat metus nisl (In varius)</p></article>
      <article class="recipe-card"><div class="thumb" role="img" aria-label="Plated vegan dish photo"></div><p>Imperdiet commodo</p></article>
      <article class="recipe-card"><div class="thumb" role="img" aria-label="Plated vegan dish photo"></div><p>Suspendisse nec tempus</p></article>
    </div>
    <a class="btn">See more ⟶</a>
    <div class="divider"></div>
  </section>

  <section class="recipe-section" style="top:706px">
    <h2 class="section-title"><span>All Recipes</span></h2>
    <div class="recipe-grid">
      <article class="recipe-card"><div class="thumb" role="img" aria-label="Plated vegan dish photo"></div><p>Porttitor varius elit lacinia</p></article>
      <article class="recipe-card"><div class="thumb" role="img" aria-label="Plated vegan dish photo"></div><p>Nam consequat metus nisl (In varius)</p></article>
      <article class="recipe-card"><div class="thumb" role="img" aria-label="Plated vegan dish photo"></div><p>Imperdiet commodo</p></article>
      <article class="recipe-card"><div class="thumb" role="img" aria-label="Plated vegan dish photo"></div><p>Suspendisse nec tempus</p></article>
      <article class="recipe-card"><div class="thumb" role="img" aria-label="Plated vegan dish photo"></div><p>Porttitor varius elit lacinia</p></article>
      <article class="recipe-card"><div class="thumb" role="img" aria-label="Plated vegan dish photo"></div><p>Nam consequat metus nisl (In varius)</p></article>
      <article class="recipe-card"><div class="thumb" role="img" aria-label="Plated vegan dish photo"></div><p>Imperdiet commodo</p></article>
      <article class="recipe-card"><div class="thumb" role="img" aria-label="Plated vegan dish photo"></div><p>Suspendisse nec tempus</p></article>
    </div>
    <a class="btn">See more ⟶</a>
    <div class="divider"></div>
  </section>
</main>

<aside class="sidebar">
  <div class="widget about" style="top:130px;height:174px">
    <h3>About Maren by the dunes</h3>
    <div class="about-photo" role="img" aria-label="Seashore at sunset with a figure by the water"></div>
    <p>On Maren by the dunes, I share some delicious recipes either my own or from other fabulous sites that I have come across, my meal plans, reviews of products and restaurants that I visit and more.</p>
    <span class="more">More ⟶</span>
  </div>
  <div class="widget follow" style="top:322px;height:67px">
    <h3>Subscribe &amp; Follow</h3>
    <div class="socials" aria-label="Social links"><span></span><span></span><span></span><span></span><span></span></div>
  </div>
  <div class="widget newsletter" style="top:406px;height:103px">
    <h3>Newsletter</h3>
    <div class="field">Your Email Address</div>
    <a class="btn">SUBSCRIBE</a>
  </div>
  <div class="widget photo-journal" style="top:527px;height:250px">
    <h3>Photo Journal</h3>
    <div class="photo-grid">
      <div role="img" aria-label="Food photo"></div><div role="img" aria-label="Food photo"></div>
      <div role="img" aria-label="Food photo"></div><div role="img" aria-label="Food photo"></div>
      <div role="img" aria-label="Food photo"></div><div role="img" aria-label="Food photo"></div>
    </div>
    <a class="btn">Follow the journal ⟶</a>
  </div>
  <div class="widget latest" style="top:795px;height:215px">
    <h3>Latest posts</h3>
    <div class="post"><div class="thumb" role="img" aria-label="Food photo"></div><div><h4>Maecenas sodales dignissim liberoid sodales</h4><small>LIFESTYLE</small></div></div>
    <div class="post"><div class="thumb" role="img" aria-label="Food photo"></div><div><h4>Maecenas sodales dignissim liberoid sodales</h4><small>TRAVEL</small></div></div>
    <div class="post"><div class="thumb" role="img" aria-label="Food photo"></div><div><h4>Maecenas sodales dignissim liberoid sodales</h4><small>LIFESTYLE</small></div></div>
    <div class="post"><div class="thumb" role="img" aria-label="Food photo"></div><div><h4>Maecenas sodales dignissim liberoid sodales</h4><small>TRAVEL</small></div></div>
  </div>
</aside>

<footer class="site-footer">
  <div class="brand">Maren by the dunes</div>
  <div class="socials" aria-label="Social links"><span></span><span></span><span></span><span></span><span></span></div>
  <div class="copy">Copyright © 2018 Maren by the dunes. All Right Reserved. Privacy Policy | Terms of Service</div>
</footer>
</body>
</html>
```